holloway paving service

Needs to have phone number 0418259730 and email markholloway@brightmail.com.au.
ABN 62318470915
name mark holloway

For all your concreting solutions
Excavation
Exposed & colour concrete
House & shed slabs
Driveways
Landing & steps

Contact Information for Business Card

ph 0418259730
email markholloway@brightmail.com.au.
ABN 62318470915
name mark holloway

```html
<!DOCTYPE html>
<html lang="en">
<head>
<meta charset="utf-8">
<title>Holloway Paving Service – Business Card</title>
<link rel="stylesheet" href="https://fonts.googleapis.com/css2?family=Lato:wght@400;700&display=swap">
<style>
  :root {
    --backdrop: #1b1b1b;
    --orange: #e4622a;
    --slate: #5b5b5b;
    --slate-dark: #4a4a4a;
    --ink: #3a3a3a;
    --paper: #ffffff;
    --paper-shade: #ececec;
  }
  * { box-sizing: border-box; margin: 0; padding: 0; }
  html, body { width: 1200px; height: 963px; overflow: hidden; background: var(--backdrop); }
  body { position: relative; font-family: "Lato", sans-serif; }

  .card {
    position: absolute; left: 240px; width: 720px; height: 411px; overflow: hidden;
    box-shadow: 0 14px 30px rgba(0,0,0,.55);
  }
  .card--front { top: 50px; background: linear-gradient(120deg, var(--paper-shade) 0%, var(--paper) 45%); }
  .card--back  { top: 502px; background: linear-gradient(135deg, var(--slate) 0%, #6a6a6a 60%, var(--slate-dark) 100%); }

  /* front */
  .name-band { position: absolute; left: 0; top: 42px; width: 520px; height: 84px; }
  .name-band svg { display: block; }
  .role { position: absolute; left: 38px; top: 52px; color: #f2f2f2; font-size: 17px; }
  .name { position: absolute; left: 38px; top: 74px; color: var(--orange); font-size: 38px; font-weight: 700; letter-spacing: 1px; text-transform: uppercase; }

  .brand { position: absolute; display: flex; align-items: center; gap: 14px; }
  .brand__square { width: 42px; height: 42px; background: var(--orange); flex: none; }
  .brand__rule { width: 2px; height: 72px; background: var(--orange); flex: none; }
  .brand__text { display: flex; flex-direction: column; gap: 4px; }
  .brand__name { color: var(--orange); font-weight: 700; font-size: 21px; line-height: 1.15; letter-spacing: 1px; text-transform: uppercase; white-space: nowrap; }
  .brand__phone { color: var(--orange); font-size: 16px; letter-spacing: 3px; }
  .card--front .brand { left: 446px; top: 136px; transform: scale(.85); transform-origin: left top; }

  .contact { position: absolute; left: 44px; top: 210px; list-style: none; display: flex; flex-direction: column; gap: 7px; }
  .contact li { display: flex; align-items: center; gap: 10px; color: var(--ink); font-size: 18px; }
  .contact svg { flex: none; }
  .contact__abn { padding-left: 24px; }
  .accent { color: var(--orange); }

  .address { position: absolute; right: 40px; bottom: 36px; text-align: right; }
  .address__town { color: var(--orange); font-size: 19px; font-weight: 700; }
  .address__region { color: var(--ink); font-size: 19px; }

  /* back */
  .card--back .brand { left: 150px; top: 130px; transform: scale(1.15); transform-origin: left top; }
  .card--back .brand__rule { height: 80px; }
  .web { position: absolute; left: 0; right: 0; top: 300px; text-align: center; color: #f0f0f0; font-size: 22px; }
</style>
</head>
<body>

<section class="card card--front">
  <div class="name-band">
    <svg width="520" height="84" viewBox="0 0 520 84"><polygon points="0,0 470,0 520,42 470,84 0,84" fill="var(--slate)"/></svg>
  </div>
  <p class="role">Director</p>
  <h1 class="name">Mark Holloway</h1>

  <div class="brand">
    <span class="brand__square"></span>
    <span class="brand__rule"></span>
    <div class="brand__text">
      <span class="brand__name">Holloway Paving<br>Service</span>
      <span class="brand__phone">0418259730</span>
    </div>
  </div>

  <ul class="contact">
    <li>
      <svg width="14" height="14" viewBox="0 0 24 24"><path d="M6.6 10.8a15 15 0 0 0 6.6 6.6l2.2-2.2a1 1 0 0 1 1-.25 11.4 11.4 0 0 0 3.6.57 1 1 0 0 1 1 1V20a1 1 0 0 1-1 1A17 17 0 0 1 3 4a1 1 0 0 1 1-1h3.5a1 1 0 0 1 1 1c0 1.25.2 2.45.57 3.57a1 1 0 0 1-.25 1z" fill="var(--orange)"/></svg>
      +61 418 259 730
    </li>
    <li>
      <svg width="14" height="14" viewBox="0 0 24 24"><rect x="2" y="5" width="20" height="14" fill="none" stroke="var(--orange)" stroke-width="2.4"/><path d="M2 6l10 7 10-7" fill="none" stroke="var(--orange)" stroke-width="2.4"/></svg>
      markholloway@brightmail.com.au
    </li>
    <li>
      <svg width="14" height="14" viewBox="0 0 24 24"><circle cx="12" cy="12" r="10" fill="none" stroke="var(--orange)" stroke-width="2.4"/><path d="M2 12h20M12 2c3 3 3 17 0 20M12 2c-3 3-3 17 0 20" fill="none" stroke="var(--orange)" stroke-width="2"/></svg>
      <span>www.<span class="accent">hollowaypaving</span>.com.au</span>
    </li>
    <li class="contact__abn"><span><span class="accent">ABN</span> 62318470915</span></li>
  </ul>

  <div class="address">
    <p class="address__town">Sorell</p>
    <p class="address__region">Hobart, Tasmania 7172</p>
  </div>
</section>

<section class="card card--back">
  <div class="brand">
    <span class="brand__square"></span>
    <span class="brand__rule"></span>
    <div class="brand__text">
      <span class="brand__name">Holloway Paving Service</span>
      <span class="brand__phone">0418259730</span>
    </div>
  </div>
  <p class="web">www.<span class="accent">hollowaypaving</span>.com.au</p>
</section>

</body>
</html>
```